Emerging automotive detailing business

I am starting a small automotive detailing business in hopes of becoming a well-known detailer to work on high end cars. I would like a card to reflect the high quality and time I put into my work. The name of the company is Bright Crest Detailing. I feel like it represents racecars getting off the line at the drag strip as well as an innuendo of "Up the Ladder". I do minor paint correction such as clay barring, multi-step buffing and polishing, waxing, hand washes, etc. I am always striving to learn more and improve my work. My goal is to have total customer satisfaction. This is a female run business but I do not want it to be very girly. Elegant is okay! I have pictures of my personal wrenfield attached, they do not need to be incorporated but if you can think of a cool way to use 1 or all of them, go for it!

Target Market(s)

Anyone that owns a vehicle. Preferably high end vehicles such as Valtori, Castellverde and Morvani but I will also happily work on any car, truck or suv no matter what brand.

Industry/Entity Type

Automotive

Contact Information for Business Card

Bright Crest Detailing
Mira Tolland
4175 Quenhollow Rd
Ashmere PA 17492
Cell phone- call/text- 717-555-0148
email- brightcrestdetails@maildrop-example.com
Instagram: @brightcrestdetailing
Facebook: facebook.com/brightcrestdetailing

Requirements
Must have
• Business name, my name, address, phone number. Listing that I do minor paint correction such as clay barring, multi-step buffing and polishing, waxing, hand washes, interior cleaning, and more. (This last part was in nice to haves but I have realized that I do really want it, so I moved it to must haves.) I want something that is different and eye-catching to my customers. Some people have done this very well with cards already submitted to me, but a lot have not. I didn't mess with the "look and feel bars" much because because I am pretty open to the overall design as long as it is not your basic run of the mill design.
Nice to have
• Something car related. Maybe an appointment time/date line. I do not have a logo, but if you would like to design one and incorporate it, that would be amazing!
Should not have
• Purple and Pink colors. Boring, basic, normal card.

```html
<!DOCTYPE html>
<html lang="en">
<head>
<meta charset="utf-8">
<title>Bright Crest Detailing – Business Card</title>
<link rel="stylesheet" href="https://fonts.googleapis.com/css2?family=Quicksand:wght@400;500&display=swap">
<style>
  :root {
    --backdrop: #f4ee2a;
    --card: #ffffff;
    --ink: #1a1a1a;
    --accent: #e8473a;
    --accent-light: #f26452;
    --rule: #555555;
  }
  * { margin: 0; padding: 0; box-sizing: border-box; }
  html, body { width: 1200px; height: 800px; overflow: hidden; }
  body {
    background: var(--backdrop);
    font-family: "Quicksand", sans-serif;
    color: var(--ink);
    position: relative;
  }
  .card {
    position: absolute;
    top: 250px;
    width: 540px;
    height: 300px;
    background: var(--card);
    overflow: hidden;
  }
  .card--front { left: 40px; }
  .card--back { left: 620px; }
  .card__swoosh { position: absolute; inset: 0; width: 540px; height: 300px; }

  /* Front */
  .brand {
    position: absolute;
    left: 0; top: 82px;
    width: 280px;
    text-align: center;
    font-size: 35px;
    font-weight: 400;
    letter-spacing: 2px;
    line-height: 46px;
    text-transform: uppercase;
  }
  .divider {
    position: absolute;
    left: 282px; top: 40px;
    width: 1.5px; height: 188px;
    background: var(--rule);
  }
  .contact {
    position: absolute;
    left: 294px; top: 56px;
    font-size: 13.5px;
    line-height: 17px;
  }
  .contact__name {
    color: var(--accent);
    font-size: 17px;
    margin-bottom: 10px;
  }
  .contact__address { margin-bottom: 9px; }
  .contact__line { display: flex; align-items: center; gap: 4px; white-space: nowrap; }
  .contact__line--email { font-size: 11.5px; }
  .icon { width: 13px; height: 13px; flex: none; }

  /* Back */
  .services {
    position: absolute;
    left: 0; top: 76px;
    width: 540px;
    text-align: center;
    font-size: 15px;
    line-height: 20px;
    text-transform: uppercase;
    letter-spacing: 0.3px;
  }
  .services__rule {
    position: absolute;
    left: 165px; top: 163px;
    width: 205px; height: 2px;
    background: linear-gradient(90deg, transparent, var(--ink) 30%, var(--ink) 70%, transparent);
  }
  .appointment {
    position: absolute;
    left: 34px; top: 192px;
    font-size: 13.5px;
    display: flex; align-items: center; gap: 4px;
  }
  .appointment__field {
    position: absolute;
    top: 223px;
    font-size: 13.5px;
  }
  .appointment__field--time { left: 54px; }
  .appointment__field--date { left: 250px; }
</style>
</head>
<body>

<section class="card card--front" aria-label="Business card front">
  <svg class="card__swoosh" viewBox="0 0 540 300" aria-hidden="true">
    <defs>
      <linearGradient id="redFront" x1="0" y1="0" x2="1" y2="0">
        <stop offset="0" stop-color="#e5412f"/>
        <stop offset="0.35" stop-color="#f26452"/>
        <stop offset="1" stop-color="#e5412f"/>
      </linearGradient>
    </defs>
    <path d="M0 218 Q300 292 540 258 L540 263 Q300 300 0 228 Z" fill="#111"/>
    <path d="M0 234 Q300 306 540 268 L540 300 L0 300 Z" fill="url(#redFront)"/>
  </svg>

  <h1 class="brand">Bright Crest<br>Detailing</h1>
  <div class="divider"></div>

  <div class="contact">
    <p class="contact__name">Mira Tolland</p>
    <p class="contact__address">4175 Quenhollow Rd<br>Ashmere, PA 17492</p>
    <p class="contact__line">
      <svg class="icon" viewBox="0 0 13 13" aria-hidden="true"><rect x="3.5" y="1" width="6" height="11" rx="1.2" fill="none" stroke="var(--accent)" stroke-width="1.3"/><circle cx="6.5" cy="10" r="0.7" fill="var(--accent)"/></svg>
      (717) 555-0148
    </p>
    <p class="contact__line contact__line--email">
      <svg class="icon" viewBox="0 0 13 13" aria-hidden="true"><rect x="1" y="3" width="11" height="7.5" fill="var(--accent)"/><path d="M1.3 3.3 L6.5 7.5 L11.7 3.3" fill="none" stroke="#fff" stroke-width="1"/></svg>
      brightcrestdetails@maildrop-example.com
    </p>
    <p class="contact__line">
      <svg class="icon" viewBox="0 0 13 13" aria-hidden="true"><rect x="1" y="1" width="11" height="11" rx="2" fill="var(--accent)"/></svg>
      @brightcrestdetailing
    </p>
    <p class="contact__line">
      <svg class="icon" viewBox="0 0 13 13" aria-hidden="true"><rect x="1" y="1" width="11" height="11" rx="2" fill="var(--accent)"/></svg>
      @brightcrestdetailing
    </p>
  </div>
</section>

<section class="card card--back" aria-label="Business card back">
  <svg class="card__swoosh" viewBox="0 0 540 300" aria-hidden="true">
    <defs>
      <linearGradient id="redBack" x1="0" y1="0" x2="1" y2="0">
        <stop offset="0" stop-color="#e5412f"/>
        <stop offset="0.5" stop-color="#f26452"/>
        <stop offset="1" stop-color="#e5412f"/>
      </linearGradient>
    </defs>
    <path d="M0 0 H540 V30 Q260 14 0 72 Z" fill="url(#redBack)"/>
    <path d="M0 76 Q260 18 540 36 L540 41 Q260 28 0 86 Z" fill="#111"/>
  </svg>

  <p class="services">Minor paint correction;<br>Claying, multi-step buffing and polishing,<br>waxing, hand washes, interior cleaning and more!</p>
  <div class="services__rule"></div>

  <p class="appointment">
    <svg class="icon" viewBox="0 0 13 13" aria-hidden="true"><rect x="1" y="2" width="11" height="10" fill="none" stroke="var(--ink)" stroke-width="1.3"/><rect x="1" y="2" width="11" height="2.5" fill="var(--ink)"/><line x1="4" y1="0.5" x2="4" y2="3" stroke="var(--ink)" stroke-width="1.2"/><line x1="9" y1="0.5" x2="9" y2="3" stroke="var(--ink)" stroke-width="1.2"/></svg>
    Your next appointment:
  </p>
  <p class="appointment__field appointment__field--time">Time:</p>
  <p class="appointment__field appointment__field--date">Date:</p>
</section>

</body>
</html>
```